Boutique custom software development company needs new business card

Our nearly 20 year old custom software development company would like to better include the fact that we are now providing Bitcoin services. These new services are B2B include education (how to acquire and securely hold Bitcoin) and integrating Bitcoin payments into existing ecommerce sites or other existing systems. Please keep the card clean and simple. Attached is our current design and some other files. vextorial.com

Target Market(s)

businesses owners interested in long term relationship

Industry/Entity Type

Custom software development and Bitcoin

Contact Information for Business Card

Dale Parker, dale@vextorial.com, vextorial.com, (888) 555-VXTRL

Font styles to use
Other font styles liked:
• monospace

Requirements
Must have
• double-sided
Nice to have
• clean and simple
Should not have
• physical address

```html
<!DOCTYPE html>
<html lang="en">
<head>
<meta charset="utf-8">
<title>Vextorial Business Card</title>
<link rel="stylesheet" href="https://fonts.googleapis.com/css2?family=Montserrat:wght@400;500;700;800&display=swap">
<style>
  :root {
    --stage: #8a8a88;
    --paper: #ffffff;
    --brand-blue: #3e72b9;
    --brand-orange: #ef7a22;
    --ink: #3a3a3a;
    --rule: #6f97cf;
    --back-soft: #dce6f4;
  }
  * { margin: 0; padding: 0; box-sizing: border-box; }
  html, body {
    width: 1200px; height: 801px; overflow: hidden;
    background: var(--stage);
    font-family: "Montserrat", Arial, sans-serif;
  }
  .stage {
    width: 1200px; height: 801px;
    display: flex; align-items: center; justify-content: center; gap: 60px;
  }
  .card {
    width: 525px; height: 300px;
    box-shadow: 0 10px 24px rgba(0,0,0,.25);
    position: relative;
    flex: none;
  }
  .card-front {
    background: var(--paper);
    display: flex; align-items: center;
    padding: 0 30px 0 34px;
  }
  .brand-block { width: 222px; flex: none; }
  .brand-name {
    font-weight: 800; font-size: 32px; letter-spacing: .5px;
    color: var(--brand-orange); line-height: 1;
    white-space: nowrap;
  }
  .brand-tagline {
    font-weight: 500; font-size: 11.5px; color: var(--brand-blue);
    line-height: 1.45; margin-top: 8px;
  }
  .divider {
    width: 1px; height: 104px; background: var(--rule);
    margin: 0 22px 0 4px; flex: none;
  }
  .contact-block { flex: 1; min-width: 0; }
  .person-name {
    font-weight: 700; font-size: 19px; color: var(--brand-blue);
    letter-spacing: .5px; text-transform: uppercase; margin-bottom: 8px;
    white-space: nowrap;
  }
  .contact-list { list-style: none; }
  .contact-item {
    display: flex; align-items: center; gap: 7px;
    font-size: 12.5px; color: var(--ink); line-height: 1.6;
    white-space: nowrap;
  }
  .contact-icon { width: 11px; height: 11px; flex: none; }
  .card-back {
    background: var(--brand-blue);
    display: flex; flex-direction: column; align-items: center; justify-content: center;
    gap: 14px;
  }
  .back-lockup { display: flex; align-items: center; gap: 14px; }
  .back-mark { width: 22px; height: 22px; background: var(--brand-orange); }
  .back-name {
    font-weight: 800; font-size: 44px; letter-spacing: 2px; color: var(--paper);
    line-height: 1;
  }
  .back-services {
    font-weight: 500; font-size: 13px; letter-spacing: 1.5px;
    color: var(--back-soft); text-transform: uppercase;
  }
</style>
</head>
<body>
<main class="stage">
  <section class="card card-front" aria-label="Business card front">
    <div class="brand-block">
      <div class="brand-name">VEXTORIAL</div>
      <div class="brand-tagline">developer of custom applications<br>&amp; bitcoin payment services</div>
    </div>
    <div class="divider"></div>
    <div class="contact-block">
      <div class="person-name">Dale Parker</div>
      <ul class="contact-list">
        <li class="contact-item">
          <svg class="contact-icon" viewBox="0 0 12 12" aria-hidden="true"><path fill="#ef7a22" d="M2.5 1h2l1 2.6-1.3 1a6 6 0 0 0 3.2 3.2l1-1.3L11 7.5v2c0 .8-.7 1.5-1.5 1.5A8.5 8.5 0 0 1 1 2.5C1 1.7 1.7 1 2.5 1z"/></svg>
          (888) 555-VXTRL
        </li>
        <li class="contact-item">
          <svg class="contact-icon" viewBox="0 0 12 12" aria-hidden="true"><rect x="0.5" y="2.5" width="11" height="7.5" rx="1" fill="#ef7a22"/><path d="M1 3l5 4 5-4" stroke="#fff" stroke-width="1" fill="none"/></svg>
          dale@vextorial.com
        </li>
        <li class="contact-item">
          <svg class="contact-icon" viewBox="0 0 12 12" aria-hidden="true"><circle cx="6" cy="6" r="5.2" fill="#ef7a22"/><path d="M1 6h10M6 .8c-2.2 2.8-2.2 7.6 0 10.4M6 .8c2.2 2.8 2.2 7.6 0 10.4" stroke="#fff" stroke-width=".8" fill="none"/></svg>
          www.vextorial.com
        </li>
      </ul>
    </div>
  </section>
  <section class="card card-back" aria-label="Business card back">
    <div class="back-lockup">
      <span class="back-mark"></span>
      <span class="back-name">VEXTORIAL</span>
    </div>
    <div class="back-services">Custom Software · Bitcoin Services</div>
  </section>
</main>
</body>
</html>
```